Brindle Sky Port needs a new upscale business card design for our high end aircraft hangar complex

Brindle Sky Port (BSP) is a large, upscale jet hangar complex in the US housing expensive aircraft. We need a new business card design, using our current logo. We will be attending a industry convention and need a card design that will stand out and be remembered by aircraft owners and private pilots.

Target Market(s)

Aircraft pilots or owners looking for a new upscale hangar

Industry/Entity Type

Airport

Contact Information for Business Card

I like to use very heavy card stock, 400#, double sided. Square, no rounded edges please.

Colors
3276b5
0255a3
85abd2

Requirements
Must have
• An expensive, classy design, vivid colors.
Nice to have
• Needs to look very expensive and classy, and have some "pop". Designer must be able to download or copy my current typeface or fonts.
• One card side might be black with the "Logo and Brindle Sky Port Double line image in blue (or try gold, or glossy black), and perhaps have a grayed out "K720 jet silhouette". The other card side would have our contact info, and perhaps the "BSP Logo only". I'd like my contact info 'stacked', not in a paragraph format.
Should not have
• Should not look "too busy". Having a double-sided card will help.

```html
<!DOCTYPE html>
<html lang="en">
<head>
<meta charset="utf-8">
<title>Brindle Sky Port – Business Card</title>
<link rel="stylesheet" href="https://fonts.googleapis.com/css2?family=Open+Sans:wght@400;600;700;800&display=swap">
<style>
  :root {
    --stage: #8e8e8e;
    --blue-light: #235f95;
    --blue-mid: #144677;
    --blue-dark: #0a2f5a;
    --black: #111111;
    --silver: #c9c9c9;
    --logo-blue: #2b62a3;
    --ink: #0d0d0d;
  }
  * { margin: 0; padding: 0; box-sizing: border-box; }
  html, body { width: 1105px; height: 1200px; overflow: hidden; }
  body {
    background: var(--stage);
    font-family: "Open Sans", Arial, sans-serif;
    position: relative;
  }
  .card {
    position: absolute;
    left: 180px;
    width: 746px;
    height: 427px;
    overflow: hidden;
    background: radial-gradient(ellipse at 38% 45%, var(--blue-light) 0%, var(--blue-mid) 50%, var(--blue-dark) 100%);
  }
  .card--front { top: 119px; }
  .card--back { top: 637px; }

  .front-shape { position: absolute; inset: 0; }

  .contact { position: absolute; left: 55px; top: 70px; color: var(--ink); }
  .contact__name { font-size: 25px; font-weight: 600; line-height: 1.2; }
  .contact__role { font-size: 19px; line-height: 1.3; margin-bottom: 14px; }
  .contact__address { font-size: 19px; line-height: 25px; margin-bottom: 10px; }
  .contact__list { list-style: none; }
  .contact__item {
    display: flex; align-items: center;
    font-size: 19px; line-height: 29px;
  }
  .contact__icon { width: 17px; height: 17px; margin-right: 14px; fill: var(--ink); }

  .brand-front {
    position: absolute; left: 400px; right: 0; top: 130px;
    text-align: center; color: var(--logo-blue);
    font-weight: 800; line-height: 1.05;
  }
  .brand-front__mark { font-size: 96px; letter-spacing: 4px; }
  .brand-front__name { font-size: 30px; letter-spacing: 1px; }

  .brand-back {
    position: absolute; left: 0; right: 0; top: 150px;
    text-align: center; color: var(--ink);
    font-weight: 800; font-size: 104px; letter-spacing: 6px; line-height: 1;
  }
  .web-back {
    position: absolute; left: 0; right: 0; top: 358px;
    text-align: center; color: var(--ink);
    font-size: 18px; font-weight: 600; letter-spacing: 8px;
  }
</style>
</head>
<body>

<section class="card card--front">
  <svg class="front-shape" width="746" height="427" viewBox="0 0 746 427">
    <defs>
      <linearGradient id="silverEdge" x1="0" y1="0" x2="0" y2="1">
        <stop offset="0" stop-color="#5a5a5a"/>
        <stop offset="0.6" stop-color="#d8d8d8"/>
        <stop offset="1" stop-color="#f2f2f2"/>
      </linearGradient>
    </defs>
    <path d="M 346 0 L 746 0 L 746 427 L 411 427 C 372 400 346 345 346 282 Z" fill="var(--black)"/>
    <path d="M 349 0 L 349 282 C 349 343 374 398 414 427" fill="none" stroke="url(#silverEdge)" stroke-width="4"/>
  </svg>

  <div class="contact">
    <p class="contact__name">Evan Hartley</p>
    <p class="contact__role">CEO/Founder</p>
    <p class="contact__address">2140 Larkspur Road<br>Fairbanks, Alaska 99701</p>
    <ul class="contact__list">
      <li class="contact__item">
        <svg class="contact__icon" viewBox="0 0 24 24"><path d="M6.6 10.8a15 15 0 0 0 6.6 6.6l2.2-2.2c.3-.3.7-.4 1-.2 1.1.4 2.3.6 3.6.6.6 0 1 .4 1 1V20c0 .6-.4 1-1 1A17 17 0 0 1 3 4c0-.6.4-1 1-1h3.5c.6 0 1 .4 1 1 0 1.3.2 2.5.6 3.6.1.3 0 .7-.2 1z"/></svg>
        907 555 0142
      </li>
      <li class="contact__item">
        <svg class="contact__icon" viewBox="0 0 24 24"><path d="M7 1h10a2 2 0 0 1 2 2v18a2 2 0 0 1-2 2H7a2 2 0 0 1-2-2V3a2 2 0 0 1 2-2zm0 3v14h10V4zm5 15.5a1.2 1.2 0 1 0 0 2.4 1.2 1.2 0 0 0 0-2.4z"/></svg>
        907 555 0187
      </li>
      <li class="contact__item">
        <svg class="contact__icon" viewBox="0 0 24 24"><path d="M6 2h12v6H6zM4 9h16a2 2 0 0 1 2 2v7h-4v4H6v-4H2v-7a2 2 0 0 1 2-2zm4 8v3h8v-3z"/></svg>
        907 555 0119
      </li>
      <li class="contact__item">
        <svg class="contact__icon" viewBox="0 0 24 24"><path d="M2 5h20v14H2zm2 2v.5l8 5 8-5V7z"/></svg>
        hello@brindleskyport.com
      </li>
      <li class="contact__item">
        <svg class="contact__icon" viewBox="0 0 24 24"><path d="M12 2a10 10 0 1 0 0 20 10 10 0 0 0 0-20zm-1 17.9A8 8 0 0 1 4.2 10.8L9 15.5v1a2 2 0 0 0 2 2zm6.9-2.5a2 2 0 0 0-1.9-1.4h-1v-3a1 1 0 0 0-1-1H8v-2h2a1 1 0 0 0 1-1V7h2a2 2 0 0 0 2-2v-.4a8 8 0 0 1 2.9 12.8z"/></svg>
        www.brindleskyport.com
      </li>
    </ul>
  </div>

  <div class="brand-front">
    <p class="brand-front__mark">BSP</p>
    <p class="brand-front__name">BRINDLE SKY PORT</p>
  </div>
</section>

<section class="card card--back">
  <p class="brand-back">BSP</p>
  <p class="web-back">www.brindleskyport.com</p>
</section>

</body>
</html>
```